Business cards and stationary design

We just completed the design of our new logo and we need to print new business cards and letterhead for our nonprofit. We are looking for a fresh new design that shows off our new logo. On letterhead, we must have a column on the right or left to include our Board of Directors (up to 45 names) (see attachment)

Industry/Entity Type

Non-Profit

Contact Information for Business Card

Standard business card with name, title, Company name, mailing address phone numbers, email address and website. Tagline on back "Bringing the homeless home"

Font styles to use
Sans Serif

Requirements
Must have
• include pertinent information above
• new logo
• fonts compatible with logo
• should use logo colors only
Nice to have
• tag lines

```html
<!DOCTYPE html>
<html lang="en">
<head>
<meta charset="utf-8">
<title>Shelter Path Alliance – Business Cards</title>
<link href="https://fonts.googleapis.com/css2?family=Michroma&family=Libre+Baskerville&display=swap" rel="stylesheet">
<style>
  :root{
    --teal:#0e6f8c;
    --teal-deep:#053a50;
    --teal-mid:#0a5a74;
    --ink:#3b3b3b;
    --paper:#ffffff;
    --bg-top:#b9b9b9;
    --bg-bottom:#3a3a3a;
    --soft-blue:#dfeef5;
    --soft-gold:#fdf3df;
  }
  *{margin:0;padding:0;box-sizing:border-box}
  html,body{width:1200px;height:1200px;overflow:hidden}
  body{background:linear-gradient(180deg,var(--bg-top),var(--bg-bottom));position:relative;font-family:"Libre Baskerville",Georgia,serif}
  .card{position:absolute;left:170px;width:860px;height:491px;border-radius:4px;overflow:hidden;box-shadow:0 14px 30px rgba(0,0,0,.35)}
  .card--front{top:70px;background:linear-gradient(135deg,var(--teal) 0%,var(--teal-mid) 45%,var(--teal-deep) 100%)}
  .card--back{top:630px;background:var(--paper)}

  .brand{position:absolute;display:flex;align-items:center;gap:16px;font-family:"Michroma",Arial,sans-serif;letter-spacing:3px}
  .brand__dot{width:22px;height:22px;border-radius:50%;flex:none}
  .brand__name{font-size:26px;line-height:1}
  .card--front .brand{left:160px;top:215px;color:#fff}
  .card--front .brand__dot{background:#fff}
  .card--front .brand__rule{position:absolute;left:160px;top:270px;width:420px;height:1px;background:rgba(255,255,255,.8)}
  .card--front .decor{position:absolute;right:0;top:40px;width:300px;height:360px}

  .card--back .brand{left:300px;top:90px;color:var(--teal)}
  .card--back .brand__dot{background:var(--teal)}
  .card--back .decor{position:absolute;right:0;top:120px;width:330px;height:371px}

  .person{position:absolute;left:60px;top:240px}
  .person__name{font-family:"Michroma",Arial,sans-serif;color:var(--teal);font-size:24px;letter-spacing:4px}
  .person__title{color:var(--ink);font-size:19px;margin-top:10px}
  .contact{position:absolute;left:80px;top:320px;list-style:none}
  .contact li{display:flex;align-items:center;gap:14px;font-size:19px;color:var(--ink);height:32px}
  .icon{width:22px;height:22px;flex:none}
  .divider{position:absolute;left:100px;top:424px;width:560px;height:1.5px;background:var(--teal)}
  .address{position:absolute;left:120px;top:438px;display:flex;align-items:center;gap:14px;font-size:19px;color:var(--ink)}
</style>
</head>
<body>

<section class="card card--front">
  <div class="brand"><span class="brand__dot"></span><span class="brand__name">SHELTER PATH ALLIANCE</span></div>
  <div class="brand__rule"></div>
  <div class="decor" role="img" aria-label="Faint tone-on-tone brand emblem area" style="background:linear-gradient(135deg,rgba(255,255,255,.06),rgba(255,255,255,0))"></div>
</section>

<section class="card card--back">
  <div class="decor" role="img" aria-label="Faint pastel brand emblem area" style="background:linear-gradient(160deg,var(--soft-gold) 0%,var(--soft-blue) 60%,#fbe9ec 100%);opacity:.8"></div>
  <div class="brand"><span class="brand__dot"></span><span class="brand__name">SHELTER PATH ALLIANCE</span></div>

  <div class="person">
    <div class="person__name">MARCUS DELANEY</div>
    <div class="person__title">Chairman</div>
  </div>

  <ul class="contact">
    <li>
      <svg class="icon" viewBox="0 0 22 22"><circle cx="11" cy="11" r="11" fill="var(--teal)"/><path d="M7.5 6.5l2 0 1 2.5-1.3 1a6 6 0 0 0 2.8 2.8l1-1.3 2.5 1v2a1 1 0 0 1-1 1A8.5 8.5 0 0 1 6.5 7.5a1 1 0 0 1 1-1z" fill="#fff"/></svg>
      <span>214.555.0187</span>
    </li>
    <li>
      <svg class="icon" viewBox="0 0 22 22"><circle cx="11" cy="11" r="11" fill="var(--teal)"/><g fill="none" stroke="#fff" stroke-width="1.2"><circle cx="11" cy="11" r="5.5"/><ellipse cx="11" cy="11" rx="2.4" ry="5.5"/><path d="M5.5 11h11"/></g></svg>
      <span>www.shelterpath.org</span>
    </li>
    <li>
      <svg class="icon" viewBox="0 0 22 22"><circle cx="11" cy="11" r="11" fill="var(--teal)"/><rect x="6" y="7.5" width="10" height="7" fill="#fff"/><path d="M6 7.5l5 4 5-4" fill="none" stroke="var(--teal)" stroke-width="1.2"/></svg>
      <span>marcus@shelterpath.org</span>
    </li>
  </ul>

  <div class="divider"></div>

  <div class="address">
    <svg class="icon" viewBox="0 0 22 22"><circle cx="11" cy="11" r="11" fill="var(--teal)"/><path d="M11 5a4 4 0 0 1 4 4c0 3-4 7.5-4 7.5S7 12 7 9a4 4 0 0 1 4-4z" fill="#fff"/><circle cx="11" cy="9" r="1.5" fill="var(--teal)"/></svg>
    <span>P.O Box 550219, Dallas, Texas 75201</span>
  </div>
</section>

</body>
</html>
```